Brake Test Training for Coal Mining

We offer Brake Test Training for Coal Mine workers. It's a legislative requirement that workers who are tasked with performing brake testing have certain competencies to do so. We test Light Vehicles and trailers, Heavy Vehicles and Mobile Mining Equipment like Graders, Scrapers and Dump Trucks.

```html
<!DOCTYPE html>
<html lang="en">
<head>
<meta charset="UTF-8">
<title>Brake Test Training for Coal Mining Workers</title>
<link href="https://fonts.googleapis.com/css2?family=Poppins:ital,wght@0,400;0,500;0,600;0,700;0,800;1,600;1,700&display=swap" rel="stylesheet">
<style>
  :root {
    --navy: #0e3358;
    --navy-deep: #0a2440;
    --yellow: #f6b21a;
    --yellow-light: #fbc43a;
    --headline-yellow: #f8c51a;
    --white: #ffffff;
    --ink: #17191c;
    --page: #e8e6e1;
  }
  * { margin: 0; padding: 0; box-sizing: border-box; }
  html, body { width: 901px; height: 1200px; overflow: hidden; }
  body {
    background: var(--page);
    font-family: "Poppins", sans-serif;
    position: relative;
  }
  .billboard {
    position: absolute;
    left: 40px; top: 395px;
    width: 820px; height: 410px;
    overflow: hidden;
    background: linear-gradient(180deg, var(--yellow-light) 0%, var(--yellow) 100%);
    box-shadow: 0 6px 14px rgba(0,0,0,0.25);
  }
  .billboard__sky {
    position: absolute; left: 0; top: 0;
    width: 100%; height: 204px;
    background: linear-gradient(100deg, var(--navy-deep) 0%, var(--navy) 60%, #1c4670 100%);
  }
  .billboard__photo {
    position: absolute;
    left: 512px; top: 96px;
    width: 308px; height: 164px;
    background: radial-gradient(ellipse at 55% 55%, #d9a25a 0%, #b98546 45%, rgba(185,133,70,0) 75%);
  }
  .headline {
    position: absolute; left: 26px; top: 12px;
    font-weight: 700; font-size: 67px; line-height: 1;
    color: var(--white); letter-spacing: 0.5px;
    white-space: nowrap;
  }
  .subheadline {
    position: absolute; left: 26px; top: 77px;
    font-weight: 700; font-size: 39px; line-height: 1;
    color: var(--headline-yellow); white-space: nowrap;
  }
  .lead {
    position: absolute; left: 31px; top: 124px;
    padding-left: 18px;
    border-left: 5px solid var(--headline-yellow);
    border-radius: 2px;
    font-weight: 500; font-size: 20px; line-height: 1.25;
    color: var(--white);
  }
  .we-test {
    position: absolute; left: 26px; top: 186px;
    width: 166px; height: 31px;
    background: var(--white); border-radius: 3px;
    font-weight: 800; font-size: 27px; line-height: 31px;
    color: var(--navy); letter-spacing: 3px;
    padding-left: 10px;
  }
  .check-item {
    position: absolute;
    display: flex; align-items: center; gap: 6px;
    font-weight: 700; font-style: italic; font-size: 19px; line-height: 1;
    color: var(--navy); white-space: nowrap;
  }
  .check-item svg { width: 13px; height: 13px; flex: none; }
  .check-item--light { left: 30px; top: 234px; }
  .check-item--trailers { left: 212px; top: 234px; }
  .check-item--heavy { left: 328px; top: 234px; }
  .check-item--mobile { left: 30px; top: 276px; }
  .check-note {
    position: absolute; left: 48px; top: 296px;
    font-weight: 600; font-style: italic; font-size: 12.5px;
    color: var(--navy); white-space: nowrap;
  }
  .brand {
    position: absolute; left: 38px; top: 328px;
    display: flex; align-items: center; gap: 12px;
  }
  .brand__dot {
    width: 40px; height: 40px; border-radius: 50%;
    background: var(--navy);
  }
  .brand__name {
    font-weight: 700; font-size: 16px; line-height: 1.2;
    color: var(--navy); letter-spacing: 1px;
  }
  .phone-panel {
    position: absolute; left: 338px; top: 268px;
    width: 482px; height: 72px;
    background: var(--navy);
    border-radius: 10px 0 0 10px;
    display: flex; align-items: center;
    padding-left: 16px; gap: 8px;
  }
  .phone-panel__icon { width: 42px; height: 42px; flex: none; }
  .phone-panel__number {
    font-weight: 700; font-size: 60px; line-height: 1;
    color: var(--white); letter-spacing: -0.5px;
    padding-top: 6px;
  }
  .website {
    position: absolute; left: 338px; top: 343px;
    font-weight: 800; font-size: 36px; line-height: 1;
    color: var(--ink); letter-spacing: 7px; white-space: nowrap;
  }
</style>
</head>
<body>
  <section class="billboard">
    <div class="billboard__sky"></div>
    <div class="billboard__photo" role="img" aria-label="Photo of a dusty wheel loader used in coal mining"></div>

    <h1 class="headline">BRAKE TEST TRAINING</h1>
    <h2 class="subheadline">FOR COAL MINING WORKERS</h2>
    <p class="lead">Workers testing brakes must meet<br>required competencies as per legislation.</p>

    <div class="we-test">WE TEST</div>

    <div class="check-item check-item--light">
      <svg viewBox="0 0 14 14"><circle cx="7" cy="7" r="7" fill="#0e3358"/><path d="M3.8 7.2l2.2 2.1 4.2-4.4" fill="none" stroke="#fff" stroke-width="1.8" stroke-linecap="round" stroke-linejoin="round"/></svg>
      Light Vehicles
    </div>
    <div class="check-item check-item--trailers">
      <svg viewBox="0 0 14 14"><circle cx="7" cy="7" r="7" fill="#0e3358"/><path d="M3.8 7.2l2.2 2.1 4.2-4.4" fill="none" stroke="#fff" stroke-width="1.8" stroke-linecap="round" stroke-linejoin="round"/></svg>
      Trailers
    </div>
    <div class="check-item check-item--heavy">
      <svg viewBox="0 0 14 14"><circle cx="7" cy="7" r="7" fill="#0e3358"/><path d="M3.8 7.2l2.2 2.1 4.2-4.4" fill="none" stroke="#fff" stroke-width="1.8" stroke-linecap="round" stroke-linejoin="round"/></svg>
      Heavy Vehicles
    </div>
    <div class="check-item check-item--mobile">
      <svg viewBox="0 0 14 14"><circle cx="7" cy="7" r="7" fill="#0e3358"/><path d="M3.8 7.2l2.2 2.1 4.2-4.4" fill="none" stroke="#fff" stroke-width="1.8" stroke-linecap="round" stroke-linejoin="round"/></svg>
      Mobile Mining Equipment
    </div>
    <p class="check-note">like Graders, Scrapers and Dump Trucks.</p>

    <div class="brand">
      <span class="brand__dot"></span>
      <span class="brand__name">KEYSTONE<br>MINE SKILLS</span>
    </div>

    <div class="phone-panel">
      <svg class="phone-panel__icon" viewBox="0 0 42 42">
        <circle cx="21" cy="21" r="20" fill="#f8c51a"/>
        <path d="M14.5 11.5c1-.8 2.2-.6 2.8.4l2 3.3c.5.9.3 2-.5 2.6l-1.3 1c.9 2.3 2.6 4.1 4.9 5.1l1-1.3c.6-.8 1.7-1 2.6-.5l3.3 2c1 .6 1.2 1.9.4 2.8l-1.6 1.8c-1 1.1-2.6 1.4-4 .8-5.4-2.2-9.6-6.4-11.8-11.8-.6-1.4-.3-3 .8-4z" fill="#0e3358"/>
        <path d="M23 12.5a7 7 0 0 1 6.5 6.5M23 16a3.6 3.6 0 0 1 3 3" fill="none" stroke="#0e3358" stroke-width="1.8" stroke-linecap="round"/>
      </svg>
      <span class="phone-panel__number">1300 555 018</span>
    </div>

    <p class="website">www.ksms.com.au</p>
  </section>
</body>
</html>
```